Early Detection and Diagnosis of Autism - Infographic

Our colors are blue, yellow, and green. A brand color pallette will be attached.

Here is all the information we want to have on our infographic:

Title: Why is Early Detection and Diagnosis of Autism So Important?
Reason 1: An early diagnosis can mean a child gains access to important therapies and resources when they can be the most effective. Without the diagnosis, most insurances won’t cover treatments like ABA therapy.
Reason 2: ABA therapy is shown to be most effective on toddlers and young children because their brains are not completely developed and have an increased potential for developing new learning pathways.
Reason 3: Children who receive early intervention have improved outcomes and increased success and independence in the long run.
We know that early detection and diagnosis works…
Stat 1: Research has shown that a diagnosis of autism at age 2 can be reliable, valid and stable.
Stat 2: Studies have shown that parents of children with ASD notice a developmental problem before their child’s first birthday. Concerns about vision and hearing were more often reported in the first year, and differences in social, communication, and fine motor skills were evident from 6 months of age.

Despite all the good that early detection and diagnosis can do, it hasn’t been as successful as it should be…
Stat 3: In 2016, the FHB conducted a report that showed that only 43 percent of children identified with autism had received comprehensive developmental evaluations by age 3.
Stat 4: According to a FHB study from 2016, even though ASD can be diagnosed as early as age 2 years, most children are not diagnosed with ASD until after age 4 years.

How can you make sure a child doesn’t miss out on key years of intervention? KNOW THE SIGNS
• By 6 months, no social smiles or other warm, joyful expressions directed at people
• By 6 months, limited or no eye contact
• By 9 months, no sharing of vocal sounds, smiles or other nonverbal communication
• By 12 months, no babbling
• By 12 months, no use of gestures to communicate (e.g. pointing, reaching, waving etc.)
• By 12 months, no response to name when called
• By 16 months, no words
• By 24 months, no meaningful, two-word phrases
• Any loss of any previously acquired speech, babbling or social skills

You can help increase the success of early detection by having your child evaluated if you see any of these signs.
Want to learn more about early detection?
Go to: maplegroveclinic.com/early-detection

Target Market(s)

Moms and Dads of Children with Autism

Industry/Entity Type

Health Care

Font styles to use
Sans Serif

Colors
f78f20
cadf82
fbee3d
fece3e
33b8a4

Requirements
Must have
• Great data visualization. Autism themed illustrations like puzzle pieces (a common theme in design work about autism). Need source file in PSD.

```html
<!DOCTYPE html>
<html lang="en">
<head>
<meta charset="utf-8">
<title>Why Is Early Detection and Diagnosis of Autism So Important?</title>
<link href="https://fonts.googleapis.com/css2?family=Bangers&family=Amatic+SC:wght@700&family=Roboto+Condensed:ital,wght@0,400;0,700;1,700&display=swap" rel="stylesheet">
<style>
:root{
  --bg:#eef8fb;
  --dot:#d6eef5;
  --navy:#1d4f91;
  --ink:#24406c;
  --sky:#5cc3de;
  --sky-deep:#3aa9cf;
  --blue:#1a66ab;
  --green:#8dc63f;
  --lime:#cadf82;
  --orange:#f78f20;
  --amber:#fece3e;
  --yellow:#fbee3d;
  --teal:#33b8a4;
  --pink:#e8577a;
  --cream:#fdf4c4;
  --white:#ffffff;
}
*{margin:0;padding:0;box-sizing:border-box}
html,body{width:1200px;height:2723px;overflow:hidden}
body{
  position:relative;
  background:var(--bg);
  background-image:radial-gradient(var(--dot) 7px,transparent 8px);
  background-size:150px 130px;
  font-family:"Roboto Condensed",Arial,sans-serif;
  color:var(--ink);
}
.abs{position:absolute}

/* header */
.tag{left:30px;top:50px;width:180px;height:54px;background:var(--navy);
  font-family:"Bangers",sans-serif;color:var(--white);font-size:28px;letter-spacing:1px;line-height:1;
  display:flex;align-items:center;justify-content:center;transform:rotate(-8deg);
  clip-path:polygon(0 0,100% 0,94% 50%,100% 100%,0 100%)}
.title{left:120px;top:24px;width:1020px;text-align:center;font-family:"Bangers",sans-serif;font-weight:400;
  font-size:66px;line-height:82px;letter-spacing:3px;color:var(--navy);
  -webkit-text-stroke:2px var(--white);paint-order:stroke fill}

/* head and reasons */
.head-art{left:40px;top:236px;width:840px;height:1016px;border-radius:46% 48% 8% 30%;
  background:linear-gradient(160deg,var(--sky) 0%,var(--sky-deep) 100%)}
.piece{display:flex;flex-direction:column;align-items:center;justify-content:center;
  font-family:"Bangers",sans-serif;color:var(--white);border-radius:12px;line-height:1}
.piece .lbl{font-size:30px;letter-spacing:1px}
.piece .num{font-size:110px;line-height:100px}
.piece.r1{left:463px;top:392px;width:245px;height:250px;background:var(--blue)}
.piece.r2{left:254px;top:662px;width:209px;height:206px;background:var(--green)}
.piece.r2 .num{color:var(--yellow)}
.piece.r3{left:463px;top:853px;width:236px;height:236px;background:var(--amber)}
.piece.r3 .num{color:var(--pink)}
.reason{left:884px;width:290px;font-weight:700;font-size:20px;line-height:26px;color:var(--ink)}
.pointer{left:0;top:0}

/* section headings */
.hand-title{font-family:"Amatic SC",sans-serif;font-weight:700;font-size:56px;line-height:50px;color:var(--navy);letter-spacing:1px}
.badge{font-family:"Bangers",sans-serif;color:var(--white);font-size:36px;line-height:1;letter-spacing:2px;white-space:nowrap;
  display:flex;align-items:center;justify-content:center}
.hand-art{border-radius:40px 0 0 40px}

/* stats */
.stat-num{font-family:"Bangers",sans-serif;font-size:56px;line-height:1}
.stat{font-size:19px;line-height:30px;color:var(--ink)}
.stat b{font-weight:700}
.ring{display:inline-flex;align-items:center;justify-content:center;width:36px;height:36px;
  border:3px solid var(--pink);border-radius:50%;font-family:"Amatic SC",sans-serif;font-size:30px;line-height:1;
  color:var(--pink);vertical-align:middle;margin:0 6px;background:var(--white)}
.ring.green{border-color:var(--green);color:var(--green)}
.ring.orange{border-color:var(--orange);color:var(--orange)}
.pct{display:inline-flex;align-items:center;justify-content:center;width:60px;height:36px;
  background:var(--orange);border-radius:50% 50% 40% 40%;color:var(--white);line-height:1;
  font-family:"Amatic SC",sans-serif;font-size:28px;vertical-align:middle;margin:0 6px}
.hl{background:linear-gradient(transparent 15%,rgba(232,87,122,.35) 15%)}
.hl.green{background:linear-gradient(transparent 15%,rgba(141,198,63,.4) 15%)}
.hl.yellow{background:linear-gradient(transparent 15%,rgba(254,206,62,.5) 15%)}
.divider{left:62px;top:1620px;width:1080px;height:44px;border:3px dashed var(--navy);border-top:none;
  font-family:"Amatic SC",sans-serif;font-weight:700;font-size:29px;color:var(--navy);letter-spacing:1px;
  text-align:center;line-height:40px;white-space:nowrap}

/* signs */
.months{left:40px;top:2334px;font-family:"Amatic SC",sans-serif;font-weight:700;font-size:48px;line-height:1;color:var(--navy)}
.month{left:209px;width:64px;height:64px;border-radius:8px;display:flex;align-items:center;justify-content:center;
  font-family:"Bangers",sans-serif;color:var(--white);font-size:38px;line-height:1}
.sign{left:300px;width:620px;font-weight:700;font-size:20px;line-height:27px;color:var(--navy)}

/* footer */
.footer{left:0;top:2595px;width:1200px;height:128px;background:var(--cream)}
.foot-note{left:112px;top:2622px;width:400px;font-style:italic;font-weight:700;font-size:20px;line-height:26px;color:var(--navy)}
.cta{left:545px;top:2612px;width:640px;border-left:5px solid var(--navy);padding-left:16px;font-family:"Bangers",sans-serif;color:var(--navy);white-space:nowrap}
.cta .row{display:flex;align-items:center;gap:12px}
.cta .small{font-size:28px;line-height:28px;width:130px;white-space:normal}
.cta .big{font-size:60px;line-height:60px;color:var(--orange);letter-spacing:2px}
.cta .go{font-size:24px;line-height:28px;letter-spacing:1px;text-align:right}
.cta .go span{font-family:"Roboto Condensed",sans-serif;font-weight:700;font-size:15px;text-transform:uppercase;color:var(--orange);margin-left:6px}
</style>
</head>
<body>

<div class="abs tag">AWARENESS</div>
<h1 class="abs title">Why is early detection and<br>diagnosis of autism so important?</h1>

<div class="abs head-art" role="img" aria-label="Illustration of a child's head in profile filled with puzzle pieces"></div>
<div class="abs piece r1"><span class="lbl">REASON</span><span class="num">1</span></div>
<div class="abs piece r2"><span class="lbl">REASON</span><span class="num">2</span></div>
<div class="abs piece r3"><span class="lbl">REASON</span><span class="num">3</span></div>

<svg class="abs pointer" width="1200" height="1100" viewBox="0 0 1200 1100">
  <g stroke="#ffffff" stroke-width="2" fill="#ffffff">
    <line x1="708" y1="444" x2="866" y2="444"/><polygon points="866,438 878,444 866,450"/>
    <line x1="780" y1="752" x2="866" y2="752"/><polygon points="866,746 878,752 866,758"/>
    <line x1="699" y1="1030" x2="866" y2="1030"/><polygon points="866,1024 878,1030 866,1036"/>
  </g>
</svg>

<p class="abs reason" style="top:431px">An early diagnosis can mean a child gains access to important therapies and resources when they can be the most effective. Without the diagnosis, most insurances won’t cover treatments like ABA therapy.</p>
<p class="abs reason" style="top:739px">ABA therapy is shown to be most effective on toddlers and young children because their brains are not completely developed and have an increased potential for developing new learning pathways.</p>
<p class="abs reason" style="top:1017px">Children who receive early intervention have improved outcomes and increased success and independence in the long run.</p>

<h2 class="abs hand-title" style="left:108px;top:1292px">We know that early detection<br>and diagnosis works</h2>
<div class="abs badge" style="left:722px;top:1352px;width:195px;height:50px;background:var(--sky-deep)">STATS</div>
<div class="abs hand-art" role="img" aria-label="Orange cartoon hand" style="left:907px;top:1300px;width:293px;height:102px;background:var(--orange)"></div>

<div class="abs hand-art" role="img" aria-label="Teal cartoon hand" style="left:0;top:1446px;width:110px;height:56px;background:var(--sky-deep);border-radius:0 30px 30px 0"></div>
<div class="abs stat-num" style="left:142px;top:1448px;color:var(--sky-deep)">1</div>
<p class="abs stat" style="left:210px;top:1456px;width:900px"><span class="hl">Research has shown that a diagnosis of autism at age</span><span class="ring">2</span> can be reliable, valid and stable.</p>

<div class="abs hand-art" role="img" aria-label="Pink cartoon hand" style="left:0;top:1526px;width:110px;height:56px;background:var(--pink);border-radius:0 30px 30px 0"></div>
<div class="abs stat-num" style="left:142px;top:1528px;color:var(--pink)">2</div>
<p class="abs stat" style="left:210px;top:1508px;width:900px"><b>Studies have shown that parents of children with ASD notice a developmental problem before their child’s first birthday. Concerns about vision and hearing were more often reported in the first year, and differences in social, <span class="hl">communication, and fine motor skills were evident from</span><span class="ring">6</span> months of age.</b></p>

<div class="abs divider">Despite all the good that early detection and diagnosis can do, it hasn’t been as successful as it should be…</div>

<div class="abs hand-art" role="img" aria-label="Yellow cartoon hand" style="left:0;top:1700px;width:110px;height:60px;background:var(--amber);border-radius:0 30px 30px 0"></div>
<div class="abs stat-num" style="left:142px;top:1706px;color:var(--amber)">3</div>
<p class="abs stat" style="left:210px;top:1700px;width:900px"><span class="hl yellow">In 2016, the FHB conducted a report that showed that only</span><span class="pct">43%</span> of children identified with autism had received comprehensive developmental evaluations by age<span class="ring orange">3</span></p>

<div class="abs hand-art" role="img" aria-label="Green cartoon hand" style="left:0;top:1800px;width:110px;height:60px;background:var(--green);border-radius:0 30px 30px 0"></div>
<div class="abs stat-num" style="left:142px;top:1806px;color:var(--green)">4</div>
<p class="abs stat" style="left:210px;top:1800px;width:900px"><b><span class="hl green">According to a FHB study from 2016, even though ASD can be diagnosed as early as age</span><span class="ring green">2</span> years, most children are not diagnosed with ASD until after age<span class="ring green">4</span> years.</b></p>

<h2 class="abs hand-title" style="left:108px;top:1895px">How can you make sure a child doesn’t miss out<br>on key years of intervention?</h2>
<div class="abs badge" style="left:726px;top:1964px;width:254px;height:50px;background:var(--green)">KNOW THE SIGNS</div>
<div class="abs hand-art" role="img" aria-label="Yellow cartoon hand" style="left:980px;top:1935px;width:220px;height:80px;background:var(--amber)"></div>

<div class="abs months">MONTHS</div>
<svg class="abs" style="left:160px;top:2150px" width="50" height="400" viewBox="0 0 50 400">
  <path d="M48 10 H14 V384 H48 M14 206 H0" fill="none" stroke="#1d4f91" stroke-width="3"/>
</svg>

<div class="abs month" style="top:2128px;background:var(--amber)">6</div>
<div class="abs month" style="top:2218px;background:var(--lime)">9</div>
<div class="abs month" style="top:2324px;background:var(--sky-deep)">12</div>
<div class="abs month" style="top:2418px;background:var(--green)">16</div>
<div class="abs month" style="top:2500px;background:var(--green)">24</div>

<div class="abs sign" style="top:2146px">•No social smiles or other warm, joyful expressions directed at people<br>•Limited or no eye contact</div>
<div class="abs sign" style="top:2236px">•No sharing of vocal sounds, smiles or other nonverbal communication</div>
<div class="abs sign" style="top:2316px">•No babbling<br>•No response to name when called<br>•No use of gestures to communicate (e.g. pointing, reaching, waving etc.)</div>
<div class="abs sign" style="top:2436px">•No words</div>
<div class="abs sign" style="top:2492px">•No meaningful, two-word phrases<br>•Any loss of any previously acquired speech, babbling or social skills</div>

<svg class="abs" style="left:920px;top:2118px" width="140" height="450" viewBox="0 0 140 450">
  <g fill="none" stroke="#e8577a" stroke-width="4">
    <circle cx="24" cy="42" r="20"/><line x1="10" y1="28" x2="38" y2="56"/>
    <circle cx="90" cy="42" r="20"/><line x1="76" y1="28" x2="104" y2="56"/>
    <circle cx="24" cy="132" r="20"/><line x1="10" y1="118" x2="38" y2="146"/>
    <circle cx="24" cy="238" r="20"/><line x1="10" y1="224" x2="38" y2="252"/>
    <circle cx="90" cy="238" r="20"/><line x1="76" y1="224" x2="104" y2="252"/>
    <circle cx="24" cy="332" r="20"/><line x1="10" y1="318" x2="38" y2="346"/>
    <circle cx="24" cy="414" r="20"/><line x1="10" y1="400" x2="38" y2="428"/>
  </g>
</svg>

<div class="abs footer"></div>
<p class="abs foot-note">You can help increase the success of early detection by having your child evaluated if you see any of these signs.</p>
<div class="abs cta">
  <div class="row"><span class="small">WANT TO MORE LEARN ABOUT</span><span class="big">EARLY DETECTION?</span></div>
  <div class="go">&#9829; GO TO:<span>maplegroveclinic.com/early-detection</span></div>
</div>

</body>
</html>
```